Flyer for the Lumen 2025 Conference

I am looking to produce a flyer for our upcoming conference, Lumen 2025. This is an annual conference that we plan to publicize on social media. The ideal designer will create a flyer that is eye-catching and effectively communicates the key information. Please see attached our logo, speaker photo, and flyer content.

Target Market(s)

All demographics

Industry/Entity Type

Christian

Font styles to use
Sans Serif

Requirements
Should not have
• Cross, church

```html
<!DOCTYPE html>
<html lang="en">
<head>
<meta charset="utf-8">
<title>Lumen 2025 Conference</title>
<link rel="stylesheet" href="https://fonts.googleapis.com/css2?family=Jost:wght@400;500;600;700;800&family=Cinzel:wght@500&display=swap">
<style>
  :root {
    --page: #ffffff;
    --sky-top: #b07a2c;
    --sky-glow: #f2b640;
    --earth-mid: #6b4218;
    --earth-dark: #1f1208;
    --accent-orange: #f0a431;
    --gold-light: #f6dc9a;
    --gold-mid: #c9993e;
    --gold-dark: #7a5520;
    --year-gold: #c8a45e;
    --navy: #0f3057;
    --panel: rgba(10, 6, 3, 0.82);
    --white: #ffffff;
  }
  * { margin: 0; padding: 0; box-sizing: border-box; }
  html, body { width: 1200px; height: 1200px; overflow: hidden; background: var(--page); }
  body { position: relative; font-family: "Jost", sans-serif; }

  .flyer {
    position: absolute; left: 211px; top: 0; width: 848px; height: 1200px; overflow: hidden;
  }
  .scene-photo {
    position: absolute; inset: 0;
    background:
      radial-gradient(ellipse 55% 35% at 55% 30%, var(--sky-glow) 0%, rgba(242,182,64,0) 70%),
      radial-gradient(ellipse 30% 40% at 50% 85%, rgba(240,170,60,0.55) 0%, rgba(240,170,60,0) 70%),
      linear-gradient(180deg, var(--sky-top) 0%, #a26a24 30%, var(--earth-mid) 60%, var(--earth-dark) 100%);
  }
  .speaker-photo {
    position: absolute; left: 120px; top: 62px; width: 554px; height: 536px;
    border-radius: 277px 277px 30px 30px;
    background: linear-gradient(180deg, rgba(90,55,25,0.55) 0%, rgba(40,70,150,0.55) 55%, rgba(30,50,110,0.35) 100%);
  }

  .speaker-name {
    position: absolute; left: 137px; top: 230px;
    color: var(--white); font-weight: 700; font-size: 19px; line-height: 22px; letter-spacing: 0.5px;
    transform: rotate(-56deg); transform-origin: left bottom; white-space: nowrap;
  }

  .brand-mark {
    position: absolute; left: 661px; top: 70px; width: 117px; height: 117px;
    background: var(--navy); display: flex; align-items: center; justify-content: center;
  }
  .brand-mark span { color: var(--white); font-weight: 600; font-size: 24px; letter-spacing: 1px; }

  .kicker {
    position: absolute; left: 0; width: 848px; top: 614px; text-align: center;
    color: var(--accent-orange); font-weight: 500; font-size: 25px; line-height: 30px; letter-spacing: 0.5px;
  }
  .event-title {
    position: absolute; left: 60px; width: 718px; top: 626px; text-align: center;
    font-weight: 800; font-size: 196px; line-height: 1; letter-spacing: 4px;
    background: linear-gradient(180deg, var(--gold-light) 0%, var(--gold-mid) 45%, var(--gold-dark) 60%, var(--gold-light) 100%);
    -webkit-background-clip: text; background-clip: text; color: transparent;
    filter: drop-shadow(0 0 1px #e9c77a);
  }
  .tagline {
    position: absolute; left: 62px; top: 808px; color: var(--white);
    font-weight: 700; font-size: 55px; line-height: 1;
    text-shadow: 0 2px 6px rgba(0,0,0,0.5);
  }
  .year {
    position: absolute; left: 640px; top: 802px; color: var(--year-gold);
    font-family: "Cinzel", serif; font-size: 60px; line-height: 1;
  }

  .info-panel {
    position: absolute; top: 935px; width: 347px; height: 139px;
    background: var(--panel); border-radius: 12px; color: var(--white);
  }
  .info-panel.schedule { left: 60px; }
  .info-panel.venue { left: 430px; text-align: center; }
  .info-panel h2 {
    color: var(--accent-orange); font-weight: 800; font-size: 23px;
    text-align: center; margin-top: 10px; letter-spacing: 0.3px;
  }
  .schedule table { margin: 6px 0 0 14px; border-collapse: collapse; font-size: 16.5px; }
  .schedule td { padding: 2px 6px 3px 0; white-space: nowrap; }
  .schedule td.day { font-weight: 700; width: 72px; }
  .venue p { font-size: 16.5px; line-height: 19px; margin-top: 8px; }

  .footer {
    position: absolute; left: 0; width: 848px; top: 1118px; text-align: center;
    color: var(--white); font-weight: 700; font-size: 17px; line-height: 21px;
    text-shadow: 0 1px 4px rgba(0,0,0,0.6);
  }
</style>
</head>
<body>
  <main class="flyer">
    <div class="scene-photo" role="img" aria-label="Golden sunrise over misty mountains with a stone path leading to a large carved stone arch"></div>
    <div class="speaker-photo" role="img" aria-label="Photo of the speaker in a blue suit seated on the stone arch"></div>

    <div class="speaker-name">Prophet Samuel Adeyo</div>

    <div class="brand-mark"><span>KAVRO</span></div>

    <p class="kicker">A PROPHETIC CONFERENCE</p>
    <h1 class="event-title">LUMEN</h1>
    <p class="tagline">The Voice of the Lord</p>
    <p class="year">2025</p>

    <section class="info-panel schedule">
      <h2>DATE &amp; TIME</h2>
      <table>
        <tr><td class="day">Friday</td><td>December 26th</td><td>6:30pm - 9:00pm</td></tr>
        <tr><td class="day">Saturday</td><td>December 27th</td><td>5:30pm - 8:00pm</td></tr>
        <tr><td class="day">Sunday</td><td>December 29th</td><td>4:30pm - 7:00pm</td></tr>
      </table>
    </section>

    <section class="info-panel venue">
      <h2>LOCATION</h2>
      <p>The Harborview Performing Arts Center<br>128 Millbrook Avenue<br>Westfield, Maine 04000</p>
    </section>

    <footer class="footer">
      Download the KAVRO App to stay updated on the event<br>
      555 014 2290 . hello@kavro.org . www.kavro.org
    </footer>
  </main>
</body>
</html>
```